MirelaStyle e-commerce website design for shopify platform

I currently have a trendy e-commerce clothing store that is primarily based off of the Southern California Style/Trends. I am looking for a redesign of my shopify template as I don't like my current image. I am looking for a sleek clean design that allows more focus on the products. I like neutral backgrounds and easy to use websites. Should be responsive to mobile devices. I would also like to have some ideas for a slide show picture that notifies customers of free shipping if possible. I do also have a theme template that I purchased through Shopify so one could set the theme up for me and edit it to what I need. My website is mirelastyle.com if you would like to look at the type of products I have. I am also looking to do a logo redesign as well- looking for a more stylish logo that would appeal to an approximate age range of 18-40 year old women. I want to be remembered, something to match the web design.

I like teal/turquoise and grey combos but I don't have to have this as the colors.

Target Market(s)

approx. 18-40

Industry/Entity Type

E-Commerce

Number of Pages Required

2 page

Requirements
Must have
• Menu bar, shopify compatible, easy to access/navigate, responsive to mobile devices, easy product upload
Nice to have
• if able ability to resize pictures all to the same size
Should not have
• not be difficult to navigate both on a reg. computer or mobile device

```html
<!DOCTYPE html>
<html lang="en">
<head>
<meta charset="utf-8">
<title>MirelaStyle — Home</title>
<link rel="stylesheet" href="https://fonts.googleapis.com/css2?family=Roboto:wght@300;400;500;700&family=Roboto+Slab:wght@400&display=swap">
<style>
:root{
  --teal:#10a7a7;
  --teal-dark:#0c8f8f;
  --teal-light:#2cc6c6;
  --accent-text:#138b8b;
  --dark:#424242;
  --darker:#3a3a3a;
  --page:#efefef;
  --card-border:#d6d6d6;
  --text:#444;
  --muted:#777;
  --price:#e0509a;
  --white:#fff;
}
*{box-sizing:border-box;margin:0;padding:0}
html,body{width:803px;height:1200px;overflow:hidden}
body{background:var(--page);font-family:"Roboto",Arial,sans-serif;color:var(--text);position:relative}
a{color:inherit;text-decoration:none}
.abs{position:absolute}

/* top bar */
.topbar{left:0;top:0;width:803px;height:27px;background:var(--dark);color:#eee;font-size:8px}
.topbar .locale{position:absolute;left:117px;top:7px;display:flex;gap:6px}
.topbar .select{height:13px;border:1px solid #5a5a5a;background:#353535;padding:0 4px;display:flex;align-items:center;gap:4px;font-size:7px}
.flag{width:9px;height:6px;background:#d44;border:1px solid #fff}
.topbar .account{position:absolute;right:115px;top:8px;display:flex;gap:5px}

/* header */
.logo{left:117px;top:48px;display:flex;align-items:center;gap:6px;font-size:25px;font-weight:500;color:#2b2b2b;letter-spacing:-.3px}
.logo .dot{width:10px;height:10px;border-radius:50%;background:var(--teal)}
.search{left:433px;top:50px;width:159px;height:25px;border:1px solid #d4d4d4;background:var(--white);display:flex}
.search span{flex:1;font-size:8px;color:#888;padding:8px 8px}
.search .go{width:27px;background:var(--teal-light);display:flex;align-items:center;justify-content:center}
.cart{left:598px;top:50px;width:90px;height:25px;border:1px solid #d4d4d4;background:var(--white);font-size:7.5px;display:flex;align-items:center;gap:5px;padding-left:6px}

/* nav */
.nav{left:117px;top:98px;width:571px;height:28px;background:linear-gradient(#21b6c0,#0f9ea6);border:1px solid #0b8d93;display:flex;justify-content:space-between;align-items:center;padding:0 12px;color:var(--white);font-size:9.5px}

/* hero */
.frame{background:var(--white);border:1px solid #dcdcdc;padding:3px}
.hero{left:117px;top:130px;width:571px;height:239px}
.hero .photo{width:100%;height:100%;background:linear-gradient(100deg,#c9c0b0 0%,#9f9a8c 30%,#3f5a6a 55%,#1e3d52 100%);position:relative}
.hero .sale{position:absolute;left:327px;top:52px;font-size:43px;font-weight:500;color:var(--teal-light);letter-spacing:.5px}
.hero .tag{position:absolute;left:328px;top:102px;font-size:17px;color:var(--white)}
.hero .shop{position:absolute;left:331px;top:140px;width:92px;height:34px;background:linear-gradient(#22c2c2,#0e9d9d);color:var(--white);font-size:12px;display:flex;align-items:center;justify-content:center}
.hero .arrows{position:absolute;right:12px;bottom:12px;display:flex;gap:3px}
.hero .arrows i{width:12px;height:12px;border-radius:50%;background:var(--white);display:flex;align-items:center;justify-content:center}

/* promo banners */
.promo{top:376px;height:117px}
.promo .photo{width:100%;height:100%;position:relative}
.promo-sale{left:117px;width:277px}
.promo-sale .photo{background:linear-gradient(90deg,#a9744a 0%,#6b5a4a 45%,#2d3c3f 100%)}
.promo-head{left:402px;width:283px}
.promo-head .photo{background:linear-gradient(90deg,#c8d9e6 0%,#b5cee0 50%,#9cc0dd 100%)}
.promo .copy{position:absolute;right:26px;top:22px;text-align:left}
.promo-sale .copy{color:var(--white);right:25px}
.promo-sale .big{font-size:30px;font-weight:500}
.promo-sale .small{font-size:6px;margin:2px 0 5px}
.promo-sale .off{font-size:20px;font-weight:500}
.promo-head .copy{right:12px;top:30px}
.promo-head .big{font-size:19px;font-weight:500;color:var(--accent-text)}
.promo-head .small{font-size:8.5px;color:#333;margin:6px 0 7px}
.promo-head .off{font-size:15px;font-weight:500;color:var(--accent-text)}

/* new arrivals */
.arrivals{left:117px;top:507px;width:570px;height:455px;background:#f7f7f7;border:1px solid #dedede}
.arrivals h2{position:absolute;left:15px;top:12px;font-size:13px;font-weight:400;color:var(--accent-text)}
.arrivals .rule{position:absolute;left:15px;top:33px;width:530px;height:1px;background:#ccc}
.grid{position:absolute;left:10px;top:48px;display:grid;grid-template-columns:repeat(4,129px);column-gap:10px;row-gap:16px}
.product{height:187px;background:var(--white);border:1px solid var(--card-border);position:relative;text-align:center}
.product .thumb{position:absolute;left:8px;top:5px;width:113px;height:121px;border:1px solid #e2e2e2}
.product .name{position:absolute;left:0;right:0;top:133px;font-size:7px;color:#333}
.product .price{position:absolute;left:0;right:0;top:146px;font-size:8.5px;color:var(--price)}
.product .add{position:absolute;left:20px;top:159px;width:88px;height:20px;background:linear-gradient(#1fb6b6,#0e9a9a);color:var(--white);font-family:"Roboto Slab",Georgia,serif;font-size:7.5px;display:flex;align-items:center;justify-content:center;gap:7px}
.tone-a{background:linear-gradient(#f5f5f5,#e4e6e0)}
.tone-b{background:linear-gradient(#f7f7f7,#e9e6e3)}
.tone-c{background:linear-gradient(#f4f4f4,#ddd2c4)}
.tone-d{background:linear-gradient(#6d6f5a,#bbb7ab)}
.tone-e{background:linear-gradient(#f4f4f4,#cfcfcf)}

/* features strip */
.features{left:110px;top:982px;width:578px;height:45px;background:var(--white);display:flex;align-items:center;font-size:8px;color:#555}
.features .feat{flex:1;display:flex;align-items:center;gap:6px;padding-left:10px;height:33px;border-right:1px dashed #bbb}
.features .feat:last-child{border-right:none;justify-content:flex-end;padding-right:8px;gap:3px}
.feat .ico{width:18px;height:18px;border-radius:3px}
.pay{width:22px;height:11px;border-radius:1px}

/* footer */
.footer{left:0;top:1035px;width:803px;height:128px;background:var(--teal);color:var(--white)}
.footer h3{font-size:12.5px;font-weight:400;letter-spacing:.2px}
.footer .col{position:absolute;top:15px}
.footer p{font-size:7px;line-height:11px}
.about{left:117px;width:125px}
.about p{margin-top:8px;text-align:justify}
.tweets{left:270px;width:125px}
.tweets .follow{position:absolute;left:88px;top:-1px;background:var(--white);color:#2a6f8a;font-size:6px;padding:2px 5px;border-radius:2px}
.tweet-head{display:flex;gap:8px;margin-top:9px}
.avatar{width:40px;height:24px;background:linear-gradient(#d9b8a8,#a77d6a)}
.tweets p.body{margin-top:8px;text-align:justify}
.followus{left:441px}
.followus ul{list-style:none;margin-top:9px}
.followus li{display:flex;align-items:center;gap:8px;font-size:8px;height:25px}
.followus li i{width:14px;height:14px;border-radius:50%;background:var(--white)}
.newsletter{left:554px;width:134px}
.newsletter p{margin-top:9px;text-align:justify}
.newsletter .field{width:134px;height:20px;background:var(--white);margin-top:8px}
.newsletter .btn{width:57px;height:20px;background:#333;font-size:7.5px;display:flex;align-items:center;justify-content:center;margin-top:7px}
.bottom{left:0;top:1163px;width:803px;height:37px;background:var(--darker);color:#eee;font-size:7.5px;display:flex;align-items:center;justify-content:center}
</style>
</head>
<body>

<div class="abs topbar">
  <div class="locale">
    <div class="select"><span class="flag"></span><svg width="5" height="4" viewBox="0 0 5 4"><path d="M0 0l2.5 3L5 0" fill="none" stroke="#ddd"/></svg></div>
    <div class="select">USD <svg width="5" height="4" viewBox="0 0 5 4"><path d="M0 0l2.5 3L5 0" fill="none" stroke="#ddd"/></svg></div>
  </div>
  <div class="account"><a>Login</a>|<a>Create an account</a>|<a>My Account</a>|<a>Wish List (0)</a></div>
</div>

<div class="abs logo"><span>MirelaStyle</span><span class="dot"></span></div>

<div class="abs search"><span>Search</span><div class="go"><svg width="12" height="12" viewBox="0 0 12 12"><circle cx="5" cy="5" r="3.6" fill="none" stroke="#fff" stroke-width="1.5"/><path d="M7.6 7.6L11 11" stroke="#fff" stroke-width="1.6"/></svg></div></div>
<div class="abs cart"><svg width="16" height="12" viewBox="0 0 16 12"><path d="M0 1h3l2 7h8l2-5H4" fill="none" stroke="#444" stroke-width="1.2"/><circle cx="6" cy="10.5" r="1.1" fill="#444"/><circle cx="12" cy="10.5" r="1.1" fill="#444"/></svg>0 item(s) - $0.00</div>

<nav class="abs nav"><a>WHAT'S NEW?</a><a>DRESSES</a><a>TOPS</a><a>BOTTOMS/ROMPERS</a><a>ACCESSORIES</a><a>SALE</a><a>A LITTLE ABOUT ME</a></nav>

<section class="abs frame hero">
  <div class="photo" role="img" aria-label="Woman in a floral summer dress standing beside a glass house under trees">
    <div class="sale">SALE 50%</div>
    <div class="tag">SEASONAL MUST HAVES</div>
    <a class="shop">SHOP NOW</a>
    <div class="arrows">
      <i><svg width="6" height="6" viewBox="0 0 6 6"><path d="M4 0.5L1.5 3 4 5.5" fill="none" stroke="#333" stroke-width="1.2"/></svg></i>
      <i><svg width="6" height="6" viewBox="0 0 6 6"><path d="M2 0.5L4.5 3 2 5.5" fill="none" stroke="#333" stroke-width="1.2"/></svg></i>
    </div>
  </div>
</section>

<section class="abs frame promo promo-sale">
  <div class="photo" role="img" aria-label="Woman in a plaid shirt and grey jacket outdoors in autumn">
    <div class="copy"><div class="big">SALE</div><div class="small">NEQUE PORRO QUISQUAM</div><div class="off">30% OFF</div></div>
  </div>
</section>
<section class="abs frame promo promo-head">
  <div class="photo" role="img" aria-label="Smiling woman wearing a patterned headband">
    <div class="copy"><div class="big">HEADBANDS</div><div class="small">NEQUE PORRO QUISQUAM</div><div class="off">SPECIAL OFFER</div></div>
  </div>
</section>

<section class="abs arrivals">
  <h2>NEW ARRIVALS</h2>
  <div class="rule"></div>
  <div class="grid">
    <div class="product"><div class="thumb tone-a" role="img" aria-label="Model in a lace bodycon dress"></div><div class="name">PRODUCT NAME</div><div class="price">$ 651.00</div><a class="add"><svg width="11" height="9" viewBox="0 0 11 9"><path d="M0 1h2l1.5 5h6l1.2-3.5H2.6" fill="#fff"/><circle cx="4" cy="7.8" r="1" fill="#fff"/><circle cx="8.5" cy="7.8" r="1" fill="#fff"/></svg>ADD TO CART</a></div>
    <div class="product"><div class="thumb tone-b" role="img" aria-label="Model in a white plunge skater dress"></div><div class="name">PRODUCT NAME</div><div class="price">$ 529.95</div><a class="add"><svg width="11" height="9" viewBox="0 0 11 9"><path d="M0 1h2l1.5 5h6l1.2-3.5H2.6" fill="#fff"/><circle cx="4" cy="7.8" r="1" fill="#fff"/><circle cx="8.5" cy="7.8" r="1" fill="#fff"/></svg>ADD TO CART</a></div>
    <div class="product"><div class="thumb tone-c" role="img" aria-label="Model in a beige maxi dress"></div><div class="name">PRODUCT NAME</div><div class="price">$ 609.95</div><a class="add"><svg width="11" height="9" viewBox="0 0 11 9"><path d="M0 1h2l1.5 5h6l1.2-3.5H2.6" fill="#fff"/><circle cx="4" cy="7.8" r="1" fill="#fff"/><circle cx="8.5" cy="7.8" r="1" fill="#fff"/></svg>ADD TO CART</a></div>
    <div class="product"><div class="thumb tone-a" role="img" aria-label="Model in a white off-shoulder top"></div><div class="name">PRODUCT NAME</div><div class="price">$ 319.95</div><a class="add"><svg width="11" height="9" viewBox="0 0 11 9"><path d="M0 1h2l1.5 5h6l1.2-3.5H2.6" fill="#fff"/><circle cx="4" cy="7.8" r="1" fill="#fff"/><circle cx="8.5" cy="7.8" r="1" fill="#fff"/></svg>ADD TO CART</a></div>
    <div class="product"><div class="thumb tone-b" role="img" aria-label="Model in a white open-back dress"></div><div class="name">PRODUCT NAME</div><div class="price">$ 651.00</div><a class="add"><svg width="11" height="9" viewBox="0 0 11 9"><path d="M0 1h2l1.5 5h6l1.2-3.5H2.6" fill="#fff"/><circle cx="4" cy="7.8" r="1" fill="#fff"/><circle cx="8.5" cy="7.8" r="1" fill="#fff"/></svg>ADD TO CART</a></div>
    <div class="product"><div class="thumb tone-d" role="img" aria-label="Model in a white tunic with black trim outdoors"></div><div class="name">PRODUCT NAME</div><div class="price">$ 529.95</div><a class="add"><svg width="11" height="9" viewBox="0 0 11 9"><path d="M0 1h2l1.5 5h6l1.2-3.5H2.6" fill="#fff"/><circle cx="4" cy="7.8" r="1" fill="#fff"/><circle cx="8.5" cy="7.8" r="1" fill="#fff"/></svg>ADD TO CART</a></div>
    <div class="product"><div class="thumb tone-e" role="img" aria-label="Model in a black strapless dress"></div><div class="name">PRODUCT NAME</div><div class="price">$ 609.95</div><a class="add"><svg width="11" height="9" viewBox="0 0 11 9"><path d="M0 1h2l1.5 5h6l1.2-3.5H2.6" fill="#fff"/><circle cx="4" cy="7.8" r="1" fill="#fff"/><circle cx="8.5" cy="7.8" r="1" fill="#fff"/></svg>ADD TO CART</a></div>
    <div class="product"><div class="thumb tone-a" role="img" aria-label="Model in a white and navy dip-dye maxi dress"></div><div class="name">PRODUCT NAME</div><div class="price">$ 319.95</div><a class="add"><svg width="11" height="9" viewBox="0 0 11 9"><path d="M0 1h2l1.5 5h6l1.2-3.5H2.6" fill="#fff"/><circle cx="4" cy="7.8" r="1" fill="#fff"/><circle cx="8.5" cy="7.8" r="1" fill="#fff"/></svg>ADD TO CART</a></div>
  </div>
</section>

<section class="abs features">
  <div class="feat"><span class="ico" style="background:#e8b64c"></span>SEE WHATS NEW ▸</div>
  <div class="feat"><span class="ico" style="background:#c8ccd2"></span>FAST FREE SHIPPING ▸</div>
  <div class="feat"><span class="ico" style="background:#e35a3c"></span>FREE GIFT WRAP ▸</div>
  <div class="feat"><span class="pay" style="background:#2f6fb4"></span><span class="pay" style="background:#d0d0d0"></span><span class="pay" style="background:#1b3f8f"></span><span class="pay" style="background:#e8732c"></span><span class="pay" style="background:#f3c24a"></span></div>
</section>

<footer class="abs footer">
  <div class="col about">
    <h3>A LITTLE ABOUT ME</h3>
    <p>My name is Lena (pronounced Lay-nah with a soft "L") and I have always loved fashion! In 2004, I moved to LA to pursue my love. I have finally made it a reality by opening my own boutique. We currently carry a variety of different</p>
  </div>
  <div class="col tweets">
    <h3>TWEETS</h3>
    <span class="follow">Follow</span>
    <div class="tweet-head"><div class="avatar" role="img" aria-label="Profile photo"></div><p>Mirela Style<br>@MirelaStyle</p></div>
    <p class="body">New Sola Playsuit added today so amazing for this fall! Shop at http://www.mirelastyle.com !</p>
  </div>
  <div class="col followus">
    <h3>FOLLOW US</h3>
    <ul><li><i></i>Facelink</li><li><i></i>Chirper</li><li><i></i>RSS</li></ul>
  </div>
  <div class="col newsletter">
    <h3>NEWSLETTER</h3>
    <p>We promise to only send you good things.</p>
    <div class="field"></div>
    <a class="btn">SING UP</a>
  </div>
</footer>

<div class="abs bottom">Copyright © 2014 All rights reserved.</div>

</body>
</html>
```